Card Design for my dog training business Brightpaw Obedience

Need a business card design for my dog training business with my new logo. Want the card to come off professional yet fun. Want it to be very eye catchy as well. I normally have these at vet clinics, pet stores, and groomers. so need it to look better than my competitors.
Target Market(s)
dog owners
Industry/Entity Type
Dog Training
Contact Information for Business Card
needs logo, my name and info
Font styles to use
Serif
Colors
0255a3
ffffff
ec1f27
000000
333333
fbfbfb
Requirements
Must have
- Brightpaw Obedience
- Felix Orland
- 415 903 2276
- info@brightpawobedience.example
- www.brightpawobedience.example

```html
<!DOCTYPE html>
<html lang="en">
<head>
<meta charset="utf-8">
<title>Brightpaw Obedience – Business Card</title>
<link href="https://fonts.googleapis.com/css2?family=EB+Garamond:ital,wght@0,500;1,400&family=Montserrat:wght@400;600&display=swap" rel="stylesheet">
<style>
  :root {
    --blue: #0255a3;
    --blue-light: #1670c2;
    --red: #ec1f27;
    --red-deep: #c8141c;
    --white: #ffffff;
    --paper: #fbfbfb;
    --ink: #000000;
    --text: #333333;
    --stage: #e9e9ec;
  }
  * { box-sizing: border-box; margin: 0; padding: 0; }
  html, body { width: 1200px; height: 914px; overflow: hidden; }
  body {
    background: var(--stage);
    display: flex;
    align-items: center;
    justify-content: center;
    gap: 90px;
  }
  .card {
    width: 400px;
    height: 700px;
    position: relative;
    box-shadow: 0 10px 30px rgba(0,0,0,.18);
    overflow: hidden;
  }

  /* Front */
  .card--front {
    background: linear-gradient(172deg,
      var(--blue) 0%, var(--blue-light) 50%,
      var(--red) 50.2%, var(--red-deep) 100%);
    color: var(--white);
  }
  .brand {
    font-family: "EB Garamond", serif;
    font-weight: 500;
    color: var(--white);
    text-align: center;
    position: absolute;
    top: 90px;
    left: 0; right: 0;
  }
  .brand__name { font-size: 40px; letter-spacing: 2px; line-height: 1; text-transform: uppercase; }
  .brand__rule { width: 230px; height: 2px; background: var(--white); margin: 10px auto 8px; }
  .brand__sub { font-size: 18px; letter-spacing: 9px; text-transform: uppercase; }

  .front-art {
    position: absolute;
    top: 255px; left: 40px;
    width: 320px; height: 215px;
    border: 5px solid var(--blue);
    background: linear-gradient(135deg, var(--white) 0%, #eaf1fa 60%, #fbe3e4 100%);
  }
  .tagline {
    position: absolute;
    bottom: 95px; left: 0; right: 0;
    text-align: center;
    font-family: "EB Garamond", serif;
    font-style: italic;
    font-size: 27px;
    line-height: 1.25;
  }

  /* Back */
  .card--back {
    background: var(--paper);
    color: var(--text);
    text-align: center;
  }
  .back-art {
    position: absolute;
    top: 70px; left: 85px;
    width: 230px; height: 130px;
    background: linear-gradient(135deg, #f2f2f2, #d9d9d9);
    border: 3px solid var(--text);
  }
  .back-brand {
    position: absolute;
    top: 215px; left: 0; right: 0;
    font-family: "EB Garamond", serif;
    font-weight: 500;
    color: var(--ink);
  }
  .back-brand .brand__name { font-size: 30px; }
  .back-brand .brand__rule { background: var(--ink); width: 190px; }
  .back-brand .brand__sub { font-size: 14px; letter-spacing: 7px; }

  .person {
    position: absolute;
    top: 345px; left: 0; right: 0;
    font-family: "Montserrat", sans-serif;
    font-weight: 600;
    font-size: 25px;
    letter-spacing: 1px;
    color: var(--blue);
    text-transform: uppercase;
  }
  .contact-icons {
    position: absolute;
    top: 430px; left: 0; right: 0;
    display: flex; justify-content: center; gap: 16px;
  }
  .contact-list {
    position: absolute;
    top: 468px; left: 0; right: 0;
    list-style: none;
    font-family: "Montserrat", sans-serif;
    font-size: 14px;
    line-height: 1.75;
    color: var(--ink);
  }
  .social {
    position: absolute;
    top: 580px; left: 0; right: 0;
    display: flex; justify-content: center; gap: 14px;
  }
  .social__box { width: 24px; height: 24px; border-radius: 3px; }
  .social__box--blue { background: var(--blue); }
  .social__box--red { background: var(--red); }
</style>
</head>
<body>

  <section class="card card--front">
    <div class="brand">
      <div class="brand__name">Brightpaw</div>
      <div class="brand__rule"></div>
      <div class="brand__sub">Obedience</div>
    </div>
    <div class="front-art" role="img" aria-label="Illustration of two dogs' heads over a regional map outline, in blue and red line art"></div>
    <p class="tagline">“Teaching dogs good manners<br>one lesson at a time.”</p>
  </section>

  <section class="card card--back">
    <div class="back-art" role="img" aria-label="Black line illustration of two dogs' heads over a regional map outline"></div>
    <div class="back-brand">
      <div class="brand__name">BRIGHTPAW</div>
      <div class="brand__rule"></div>
      <div class="brand__sub">Obedience</div>
    </div>
    <h1 class="person">Felix Orland</h1>

    <div class="contact-icons">
      <svg width="18" height="18" viewBox="0 0 24 24" aria-label="Phone"><path fill="var(--red)" d="M6.6 10.8a15 15 0 0 0 6.6 6.6l2.2-2.2a1 1 0 0 1 1-.25 11.4 11.4 0 0 0 3.6.57 1 1 0 0 1 1 1V20a1 1 0 0 1-1 1A17 17 0 0 1 3 4a1 1 0 0 1 1-1h3.5a1 1 0 0 1 1 1c0 1.25.2 2.45.57 3.57a1 1 0 0 1-.25 1z"/></svg>
      <svg width="20" height="18" viewBox="0 0 24 20" aria-label="Email"><rect x="1" y="3" width="22" height="14" rx="1.5" fill="var(--red)"/><path d="M2 4l10 7 10-7" stroke="var(--white)" stroke-width="1.6" fill="none"/></svg>
      <svg width="18" height="18" viewBox="0 0 24 24" aria-label="Website"><g fill="none" stroke="var(--red)" stroke-width="1.8"><circle cx="12" cy="12" r="10"/><ellipse cx="12" cy="12" rx="4.5" ry="10"/><path d="M2 12h20M4 6.5h16M4 17.5h16"/></g></svg>
    </div>

    <ul class="contact-list">
      <li>415 903 2276</li>
      <li>info@brightpawobedience.example</li>
      <li>www.brightpawobedience.example</li>
    </ul>

    <div class="social">
      <span class="social__box social__box--blue"></span>
      <span class="social__box social__box--red"></span>
    </div>
  </section>

</body>
</html>
```